Income Tax Flyer - Updates Needed

Just need to update this flyer design and give it a new look. We would like to keep all the same wording but make it stand out a little more. Our selling point is the "Same Day Tax Advance up to $6,000"

Lending, Small Loans, Tax Services, Title Loans, Personal Loans

```html
<!DOCTYPE html>
<html lang="en">
<head>
<meta charset="utf-8">
<title>Same Day Tax Advance Flyer</title>
<link href="https://fonts.googleapis.com/css2?family=DM+Serif+Display&family=DM+Serif+Text&display=swap" rel="stylesheet">
<style>
  :root {
    --green: #0f5a2e;
    --brown: #6b4a2a;
    --red: #c71f25;
    --white: #ffffff;
    --ink: #23262b;
    --photo-a: #b7b3ac;
    --photo-b: #2b3550;
  }
  * { margin: 0; padding: 0; box-sizing: border-box; }
  html, body { width: 848px; height: 1200px; overflow: hidden; background: var(--white); }
  .flyer { position: relative; width: 848px; height: 1200px; overflow: hidden; background: var(--white); font-family: "DM Serif Text", Georgia, serif; }
  .backdrop { position: absolute; inset: 0; }
  .headline { position: absolute; left: 76px; top: 44px; width: 470px; color: var(--white);
    font-family: "DM Serif Display", Georgia, serif; font-weight: 400; font-size: 68px; line-height: 78px; }
  .offer { position: absolute; left: 76px; top: 304px; color: var(--white);
    font-family: "DM Serif Display", Georgia, serif; font-size: 35px; white-space: nowrap; }
  .brand { position: absolute; left: 590px; top: 104px; width: 222px; text-align: center; color: var(--white);
    font-family: "DM Serif Display", Georgia, serif; }
  .brand-name { font-size: 36px; line-height: 38px; white-space: nowrap; }
  .brand-sub { font-size: 10px; letter-spacing: 3.4px; line-height: 16px; margin-top: 6px; white-space: nowrap; }
  .tagline { position: absolute; left: 76px; top: 444px; color: var(--white);
    font-family: "DM Serif Display", Georgia, serif; font-size: 31px; line-height: 43px; }
  .features { position: absolute; left: 74px; top: 558px; list-style: none; }
  .feature { position: relative; height: 80px; display: flex; align-items: center; }
  .feature-badge { width: 74px; height: 74px; flex: none; }
  .feature-text { margin-left: 10px; color: var(--white); font-size: 15.5px; line-height: 21px; width: 160px; }
  .contact-title { position: absolute; left: 144px; top: 920px; color: var(--ink);
    font-family: "DM Serif Display", Georgia, serif; font-weight: 400; font-size: 35px; }
  .contact-list { position: absolute; left: 144px; top: 989px; list-style: none; color: var(--ink); font-size: 19px; }
  .contact-item { display: flex; align-items: flex-start; gap: 8px; line-height: 26px; margin-bottom: 18px; }
  .contact-item svg { flex: none; margin-top: 3px; }
  .contact-item.phone span { margin-left: 4px; }
</style>
</head>
<body>
<main class="flyer">
  <svg class="backdrop" width="848" height="1200" viewBox="0 0 848 1200">
    <defs>
      <linearGradient id="brandSweep" x1="0" y1="0" x2="1" y2="0">
        <stop offset="0" stop-color="var(--green)"/>
        <stop offset="0.45" stop-color="var(--brown)"/>
        <stop offset="1" stop-color="var(--red)"/>
      </linearGradient>
      <linearGradient id="photoTone" x1="0" y1="0" x2="1" y2="1">
        <stop offset="0" stop-color="var(--photo-a)"/>
        <stop offset="0.6" stop-color="#8a7d70"/>
        <stop offset="1" stop-color="var(--photo-b)"/>
      </linearGradient>
    </defs>
    <path role="img" aria-label="Tinted background photo of a model house and keys"
          d="M0 0 H848 V915 L541 909 C300 890 40 860 0 700 Z" fill="url(#brandSweep)"/>
    <polygon points="848,935 807,975 848,1006" fill="var(--red)"/>
    <rect x="433.5" y="429.5" width="497" height="497" rx="60" fill="var(--white)" transform="rotate(45 682 678)"/>
    <rect role="img" aria-label="Photo of a smiling advisor meeting a client at an office desk"
          x="478" y="474" width="408" height="408" rx="45" fill="url(#photoTone)" transform="rotate(45 682 678)"/>
  </svg>

  <h1 class="headline">Same Day Tax Advance up to $6,000</h1>
  <p class="offer">Apply Here For $5,000-$6,000 Today!</p>

  <div class="brand">
    <div class="brand-name">Larkmoor Vale</div>
    <div class="brand-sub">FINANCIAL GROUP</div>
  </div>

  <p class="tagline">File your taxes and apply<br>for an Easy Advance!</p>

  <ul class="features">
    <li class="feature">
      <svg class="feature-badge" viewBox="0 0 74 74">
        <rect x="14" y="14" width="46" height="46" rx="5" fill="var(--white)" transform="rotate(45 37 37)"/>
        <circle cx="37" cy="37" r="13" fill="none" stroke="var(--brown)" stroke-width="1.4" stroke-dasharray="3 2"/>
        <text x="37" y="40.5" text-anchor="middle" font-size="9" font-family="Arial, sans-serif" fill="var(--brown)">24/7</text>
      </svg>
      <span class="feature-text">Available In 24 Hours or Less</span>
    </li>
    <li class="feature">
      <svg class="feature-badge" viewBox="0 0 74 74">
        <rect x="14" y="14" width="46" height="46" rx="5" fill="var(--white)" transform="rotate(45 37 37)"/>
        <path d="M33 27 h8 l-2 4 c6 3 8 8 6 12 h-16 c-2-4 0-9 6-12 z" fill="none" stroke="var(--red)" stroke-width="1.4"/>
        <text x="37" y="41" text-anchor="middle" font-size="8" font-family="Arial, sans-serif" fill="var(--red)">$</text>
        <path d="M24 47 h6 l10 3 h8" fill="none" stroke="var(--green)" stroke-width="1.4"/>
      </svg>
      <span class="feature-text">Choose Your Loan Amount</span>
    </li>
    <li class="feature">
      <svg class="feature-badge" viewBox="0 0 74 74">
        <rect x="14" y="14" width="46" height="46" rx="5" fill="var(--white)" transform="rotate(45 37 37)"/>
        <rect x="33" y="26" width="12" height="20" rx="1" fill="none" stroke="var(--red)" stroke-width="1.4"/>
        <circle cx="39" cy="36" r="3" fill="none" stroke="var(--red)" stroke-width="1.2"/>
        <rect x="26" y="38" width="5" height="10" fill="none" stroke="var(--green)" stroke-width="1.4"/>
      </svg>
      <span class="feature-text">Quick and Easy</span>
    </li>
  </ul>

  <h2 class="contact-title">Contact Us</h2>
  <ul class="contact-list">
    <li class="contact-item phone">
      <svg width="22" height="22" viewBox="0 0 24 24"><path d="M6.6 10.8a15 15 0 0 0 6.6 6.6l2.2-2.2a1 1 0 0 1 1-.25 11.4 11.4 0 0 0 3.6.6 1 1 0 0 1 1 1V20a1 1 0 0 1-1 1A17 17 0 0 1 3 4a1 1 0 0 1 1-1h3.5a1 1 0 0 1 1 1c0 1.25.2 2.45.6 3.6a1 1 0 0 1-.25 1z" fill="var(--red)"/></svg>
      <span>+1 (555) 010 0199</span>
    </li>
    <li class="contact-item">
      <svg width="20" height="20" viewBox="0 0 24 24" fill="none" stroke="var(--red)" stroke-width="2"><circle cx="12" cy="12" r="10"/><path d="M2 12h20M12 2c3 3 3 17 0 20M12 2c-3 3-3 17 0 20"/></svg>
      <span>www.ledgerlineflyer.com</span>
    </li>
    <li class="contact-item">
      <svg width="20" height="16" viewBox="0 0 20 16"><rect width="20" height="16" rx="1" fill="var(--red)"/><path d="M1 2l9 7 9-7" fill="none" stroke="var(--white)" stroke-width="1.6"/></svg>
      <span>info@ledgerlineflyer.com</span>
    </li>
    <li class="contact-item">
      <svg width="20" height="22" viewBox="0 0 24 26"><path d="M12 1a8 8 0 0 0-8 8c0 6 8 15 8 15s8-9 8-15a8 8 0 0 0-8-8z" fill="var(--red)"/><circle cx="12" cy="9" r="3" fill="var(--white)"/></svg>
      <span>Lorem ipsum dolor sit<br>amet</span>
    </li>
  </ul>
</main>
</body>
</html>
```